Business Card Design - Amberfield Court

We are looking at a new design for our business cards that has a modern and professional look. We run a residential aged care facility focussing on the care of residents. The cards will be used for potential clients, consultants and business opportunities in this sector. Blue and white is our main colours and would to see these colours incorporated in the design.
Industry/Entity Type
Business
Contact Information for Business Card
Amberfield Court, Darren Walsh, dwalsh@amberfieldcourt.com.au, Finance Manager, 0472 639 208, BCom, 37 Marrabel Crescent, Brindle Vale, Qld 4093.
Look and feel
Each slider illustrates characteristics of the customer's brand and the style your logo design should communicate.

```html
<!DOCTYPE html>
<html lang="en">
<head>
<meta charset="utf-8">
<title>Amberfield Court – Business Card</title>
<link rel="stylesheet" href="https://fonts.googleapis.com/css2?family=Fira+Sans+Condensed:ital,wght@0,300;0,400;0,600;1,300&display=swap">
<style>
  :root {
    --page: #e9ebec;
    --card-white: #ffffff;
    --blue: #5f9fb4;
    --blue-back-a: #6fa9bf;
    --blue-back-b: #3c7288;
    --text-grey: #4a4f52;
    --text-title: #5c6c74;
  }
  * { box-sizing: border-box; margin: 0; padding: 0; }
  html, body { width: 1200px; height: 1023px; overflow: hidden; }
  body {
    background: var(--page);
    font-family: "Fira Sans Condensed", Arial, sans-serif;
    position: relative;
  }
  .card {
    position: absolute;
    width: 600px;
    height: 344px;
    border-radius: 4px;
    box-shadow: 0 10px 26px rgba(0,0,0,.18);
    overflow: hidden;
  }
  /* Front */
  .card-front { left: 70px; top: 110px; background: var(--card-white); }
  .front-illustration {
    position: absolute; right: 0; top: 0;
    width: 330px; height: 222px;
    border-radius: 160px 0 0 0;
    background: linear-gradient(160deg, #7fb3c5 0%, var(--blue) 60%);
  }
  .brand-mark {
    position: absolute; left: 30px; top: 152px;
    display: flex; align-items: center; gap: 10px;
  }
  .brand-dot { width: 30px; height: 30px; border-radius: 50%; background: var(--blue); }
  .brand-name { font-size: 22px; font-weight: 400; color: var(--text-title); }
  .person-name {
    position: absolute; left: 30px; top: 218px;
    font-size: 24px; font-weight: 600; color: var(--blue);
    text-transform: uppercase; letter-spacing: .5px; line-height: 28px;
  }
  .divider {
    position: absolute; left: 205px; top: 232px;
    width: 285px; height: 2px; background: var(--blue);
  }
  .person-role {
    position: absolute; left: 30px; top: 251px;
    font-size: 14px; color: var(--text-grey); letter-spacing: .5px;
    text-transform: uppercase;
  }
  .contact-list {
    position: absolute; left: 30px; top: 282px;
    list-style: none; font-size: 14px; color: var(--text-grey);
  }
  .contact-list li { display: flex; align-items: center; gap: 7px; margin-bottom: 4px; }
  .contact-list svg { width: 13px; height: 13px; }
  .address {
    position: absolute; right: 24px; top: 246px;
    text-align: right; font-size: 14px; line-height: 1.45;
    color: var(--text-grey); text-transform: uppercase; letter-spacing: .5px;
  }
  .front-band {
    position: absolute; right: 0; bottom: 0;
    width: 100px; height: 12px; background: var(--blue);
  }
  /* Back */
  .card-back {
    left: 530px; top: 560px;
    background: linear-gradient(135deg, var(--blue-back-a) 0%, var(--blue-back-b) 100%);
  }
  .back-name {
    position: absolute; left: 40px; top: 48px;
    font-size: 30px; font-weight: 400; color: var(--text-title);
  }
  .back-tagline {
    position: absolute; left: 42px; top: 92px;
    font-size: 18px; font-style: italic; font-weight: 300; color: #fff;
  }
  .back-decoration {
    position: absolute; left: 200px; bottom: 0;
    width: 400px; height: 180px;
    background: radial-gradient(ellipse at 50% 80%, rgba(40,90,112,.45) 0%, rgba(40,90,112,0) 70%);
  }
</style>
</head>
<body>
  <section class="card card-front">
    <div class="front-illustration" role="img" aria-label="Illustration of a carer with an elderly resident"></div>
    <div class="brand-mark">
      <span class="brand-dot"></span>
      <span class="brand-name">Amberfield Court</span>
    </div>
    <h1 class="person-name">Darren Walsh</h1>
    <div class="divider"></div>
    <p class="person-role">Finance Manager</p>
    <ul class="contact-list">
      <li>
        <svg viewBox="0 0 13 13"><rect width="13" height="13" rx="2" fill="#5f9fb4"/><path d="M4 3h2l1 2-1 1a5 5 0 0 0 2 2l1-1 2 1v2h-1A7 7 0 0 1 3 4z" fill="#fff"/></svg>
        0472 639 208
      </li>
      <li>
        <svg viewBox="0 0 13 13"><rect width="13" height="13" rx="2" fill="#5f9fb4"/><rect x="2.5" y="4" width="8" height="5.5" fill="none" stroke="#fff"/><path d="M2.5 4l4 3 4-3" fill="none" stroke="#fff"/></svg>
        dwalsh@amberfieldcourt.com.au
      </li>
    </ul>
    <p class="address">BCom, 37 Marrabel Crescent<br>Brindle Vale, Qld 4093.</p>
    <div class="front-band"></div>
  </section>

  <section class="card card-back">
    <h2 class="back-name">Amberfield Court</h2>
    <p class="back-tagline">Caring for every resident</p>
    <div class="back-decoration" role="img" aria-label="Faint illustration of a carer with a resident"></div>
  </section>
</body>
</html>
```